KOVA! Card

The single side "business card" will be utilized to write down product information for our customers. The card needs to include our logo in josefin font and read KOVA! on the front. Our brand colors are espresso brown and copper. The back needs to be white (blank) to allow us to write information down. We want modern, bold, clean and fun.
I have attached a copy of our logo but you do not have to utilize exactly as shown.

```html
<!DOCTYPE html>
<html lang="en">
<head>
<meta charset="utf-8">
<title>KOVA! Card</title>
<link href="https://fonts.googleapis.com/css2?family=Josefin+Sans:wght@300&display=swap" rel="stylesheet">
<style>
  :root {
    --page: #e8e6ea;
    --espresso: #28170f;
    --copper: #c4661f;
    --copper-dark: #6e3b1c;
    --ink: #1f120b;
  }
  html, body {
    margin: 0;
    width: 1200px;
    height: 900px;
    overflow: hidden;
    background: var(--page);
  }
  .card {
    position: absolute;
    left: 110px;
    top: 170px;
    width: 980px;
    height: 559px;
    background: var(--espresso);
    box-shadow: 0 6px 18px rgba(0, 0, 0, 0.25);
    font-family: "Josefin Sans", sans-serif;
    overflow: hidden;
  }
  .motif-area {
    position: absolute;
    left: 430px;
    top: 50px;
    width: 538px;
    height: 490px;
    background: linear-gradient(160deg, var(--espresso) 0%, var(--copper-dark) 45%, var(--copper) 100%);
  }
  .brand {
    position: absolute;
    left: 115px;
    top: 214px;
    color: var(--copper);
  }
  .brand__name {
    margin: 0;
    font-weight: 300;
    font-size: 70px;
    line-height: 1;
    letter-spacing: 1px;
  }
  .brand__tagline {
    margin: 8px 0 0 2px;
    font-weight: 300;
    font-size: 25px;
    letter-spacing: 0.5px;
  }
  .headline {
    position: absolute;
    left: 652px;
    top: 428px;
    margin: 0;
    font-weight: 300;
    font-size: 62px;
    line-height: 1;
    letter-spacing: 6px;
    color: var(--ink);
  }
</style>
</head>
<body>
  <div class="card">
    <div class="motif-area" role="img" aria-label="Angular copper and espresso triangle motif"></div>
    <div class="brand">
      <p class="brand__name">vellmar</p>
      <p class="brand__tagline">Jewelry &amp; Design Studio</p>
    </div>
    <p class="headline">KOVA!</p>
  </div>
</body>
</html>
```